Meridale Bed Company Needs Business Card

Looking for a very nice looking business card. Creative but not extravagant. We sell beds and pillows across the U.S. and need something professional but catchy. I have attached the logo.

Name : Devin Holt
Title : President
Phone : (800) 471-2960
Email: sleep@quilmora.com
Website: www.quilmora.com

Can be single-sided or double-sided
horizontal or vertical

Can use Blues/Greys

Target Market(s)

Mass Market

Industry/Entity Type

Retail

Contact Information for Business Card

Name : Devin Holt
Title : President
Phone : (800) 471-2960
Email: sleep@quilmora.com
Website: www.quilmora.com

Requirements
Must have
• Clean, Modern, Smooth
• Can use Blues/Greys
• On the other side without the information - have something simple like www.quilmora.com or our logo
Nice to have
• Surprise me
Should not have
• Nothing crazy, nothing cluttered

```html
<!DOCTYPE html>
<html lang="en">
<head>
<meta charset="utf-8">
<title>Meridale Bed Company – Business Card</title>
<link rel="stylesheet" href="https://fonts.googleapis.com/css2?family=Open+Sans:wght@400;600&display=swap">
<style>
  :root {
    --brand-blue: #35a6d8;
    --ink: #2b2b2b;
    --card-white: #ffffff;
    --backdrop: #eceef0;
  }
  * { margin: 0; padding: 0; box-sizing: border-box; }
  html, body {
    width: 1200px; height: 900px; overflow: hidden;
    background: var(--backdrop);
  }
  .canvas { position: relative; width: 1200px; height: 900px; }

  .card {
    position: absolute;
    width: 555px; height: 343px;
    box-shadow: 0 6px 18px rgba(0,0,0,0.12);
    overflow: hidden;
  }

  /* Front */
  .card-front { left: 238px; top: 62px; background: var(--card-white); }
  .card-front .bands { position: absolute; inset: 0; }
  .person {
    position: absolute; left: 44px; top: 34px;
    font-family: "Open Sans", sans-serif;
  }
  .person-name { font-size: 24px; font-weight: 600; color: var(--brand-blue); line-height: 1.2; }
  .person-title { font-size: 19px; font-weight: 400; color: var(--ink); line-height: 1.35; margin-top: 4px; }

  .brand-name {
    font-family: "Open Sans", sans-serif;
    font-weight: 400;
    line-height: 1;
    white-space: nowrap;
  }
  .card-front .brand-name {
    position: absolute; right: 46px; top: 128px;
    font-size: 60px; color: var(--brand-blue);
  }

  .contact {
    position: absolute; left: 38px; top: 214px;
    list-style: none;
    font-family: "Open Sans", sans-serif;
    font-size: 19px; color: var(--ink);
  }
  .contact li { display: flex; align-items: center; height: 28px; }
  .contact svg { width: 15px; height: 15px; margin-right: 11px; fill: var(--brand-blue); flex: none; }

  /* Back */
  .card-back {
    left: 457px; top: 518px; width: 560px;
    background: var(--brand-blue);
    display: flex; align-items: center; justify-content: center;
  }
  .card-back .brand-name { font-size: 60px; color: var(--card-white); margin-top: -4px; }
</style>
</head>
<body>
<main class="canvas">

  <section class="card card-front" aria-label="Business card front">
    <svg class="bands" viewBox="0 0 555 343" preserveAspectRatio="none" aria-hidden="true">
      <polygon points="0,0 555,0 555,26 0,9" fill="var(--brand-blue)"/>
      <polygon points="0,318 555,334 555,343 0,343" fill="var(--brand-blue)"/>
    </svg>

    <div class="person">
      <p class="person-name">Devin Holt</p>
      <p class="person-title">President</p>
    </div>

    <p class="brand-name">quilmora</p>

    <ul class="contact">
      <li>
        <svg viewBox="0 0 24 24" aria-hidden="true"><path d="M6.6 10.8a15.1 15.1 0 0 0 6.6 6.6l2.2-2.2c.3-.3.7-.4 1-.2 1.1.4 2.3.6 3.6.6.6 0 1 .4 1 1V20c0 .6-.4 1-1 1A17 17 0 0 1 3 4c0-.6.4-1 1-1h3.5c.6 0 1 .4 1 1 0 1.3.2 2.5.6 3.6.1.3 0 .7-.2 1z"/></svg>
        (800) 471-2960
      </li>
      <li>
        <svg viewBox="0 0 24 24" aria-hidden="true"><path d="M2 5h20v14H2V5zm2 2v.3l8 5.6 8-5.6V7H4z"/></svg>
        sleep@quilmora.com
      </li>
      <li>
        <svg viewBox="0 0 24 24" aria-hidden="true"><circle cx="12" cy="12" r="10"/><path d="M2 12h20M12 2c3 3 3 17 0 20M12 2c-3 3-3 17 0 20" fill="none" stroke="var(--card-white)" stroke-width="1.5"/></svg>
        www.quilmora.com
      </li>
    </ul>
  </section>

  <section class="card card-back" aria-label="Business card back">
    <p class="brand-name">quilmora</p>
  </section>

</main>
</body>
</html>
```